Pay-Per-Use Production Space Warehouse/Factory/Production Space

Please refer to project requirements as attached/included. This is an introductory marketing Info graphic to capture attention or create awareness to a new, epic and unique business value preposition and business model for customer to easily launch new products/services and robust supply chain. This is a win win revolutionary business solution compare with traditional or conventional methods of outsourcing or DIY design, build, finance, operate and maintain. PROJECT Requirement to info graphic designer
1) Subject to confidentiality and all rights reserved
2) Below are some photos which you may consider to use for this work
3) Clarify and verify with us if there are any questions related to this work and design

Target Market(s)

Global, (Life sciences, food, others)

Industry/Entity Type

Medical And Science

Requirements
Must have
• Dynamic background template.
Should not have
• Monotonous and un-creative designs

```html
<!DOCTYPE html>
<html lang="en">
<head>
<meta charset="utf-8">
<title>Pay-Per-Use Production Space</title>
<link href="https://fonts.googleapis.com/css2?family=Montserrat:wght@400;500;700;800&display=swap" rel="stylesheet">
<style>
  :root {
    --orange: #d9653a;
    --orange-text: #e5532a;
    --red: #b5282a;
    --red-dark: #8f1c1d;
    --ink: #4a4a4a;
    --white: #ffffff;
    --divider: #9a9a9a;
    --purple: #4c3f9e;
    --green: #5c9a52;
    --scarlet: #d52d31;
  }
  * { margin: 0; padding: 0; box-sizing: border-box; }
  html, body { width: 848px; height: 1200px; overflow: hidden; background: var(--white); }
  body { font-family: "Montserrat", Arial, sans-serif; position: relative; }

  .hero-photo {
    position: absolute; left: 0; top: 0; width: 848px; height: 843px;
    background:
      radial-gradient(ellipse 420px 300px at 560px 330px, rgba(255,252,240,0.85), rgba(255,255,255,0) 70%),
      linear-gradient(180deg, #b3aa9c 0%, #cfc8bb 30%, #a9a59f 60%, #5e5b56 85%, #4a4846 100%);
  }
  .chevron { position: absolute; left: 0; top: 0; }

  .offer-panel {
    position: absolute; left: 77px; top: 402px; width: 393px; height: 360px;
    background: rgba(217, 101, 58, 0.86);
    color: var(--white); text-align: center;
  }
  .offer-kicker { font-weight: 700; font-size: 13.5px; margin-top: 12px; }
  .offer-headline { font-weight: 800; font-size: 41px; line-height: 37px; margin-top: 12px; letter-spacing: -0.5px; }
  .offer-headline sup { font-size: 28px; vertical-align: 10px; margin-left: 4px; }
  .offer-icons { display: flex; justify-content: center; gap: 24px; margin-top: 10px; }
  .offer-icon {
    width: 90px; height: 90px; border-radius: 50%;
    background: var(--red); border: 2px solid var(--red-dark);
    display: flex; align-items: center; justify-content: center;
  }
  .offer-terms { font-weight: 800; font-size: 22.5px; line-height: 27.5px; margin-top: 11px; letter-spacing: -0.2px; }

  .how-title {
    position: absolute; left: 277px; top: 937px;
    color: var(--orange-text); font-weight: 500; font-size: 23px; letter-spacing: 0.3px;
  }
  .pillar { position: absolute; top: 981px; width: 170px; }
  .pillar-badge {
    width: 84px; height: 84px; border-radius: 50%;
    display: flex; align-items: center; justify-content: center;
  }
  .pillar-label { color: var(--ink); font-weight: 500; font-size: 11.5px; line-height: 14px; letter-spacing: 0.4px; }
  .pillar--design { left: 277px; }
  .pillar--design .pillar-badge { background: radial-gradient(circle at 35% 30%, #5d52b8, var(--purple) 60%, #2d2468); }
  .pillar--design .pillar-label { margin-top: 12px; }
  .pillar--model { left: 450px; }
  .pillar--model .pillar-badge { background: radial-gradient(circle at 35% 30%, #7db56f, var(--green) 60%, #2f5a2a); }
  .pillar--model .pillar-label { margin-top: 19px; }
  .pillar--practice { left: 624px; width: 200px; }
  .pillar--practice .pillar-badge { background: radial-gradient(circle at 35% 30%, #ef4a4c, var(--scarlet) 60%, #7e1518); }
  .pillar--practice .pillar-label { margin-top: 19px; }
  .divider { position: absolute; top: 988px; width: 1px; height: 133px; background: var(--divider); }
  .footnote { position: absolute; left: 279px; top: 1142px; font-size: 8px; color: var(--ink); letter-spacing: 1px; }
</style>
</head>
<body>
  <div class="hero-photo" role="img" aria-label="Photo of a clean stainless-steel production room with a mixing vessel and process equipment"></div>

  <svg class="chevron" width="848" height="930" viewBox="0 0 848 930">
    <defs>
      <linearGradient id="chevronShade" x1="0" y1="0" x2="0" y2="1">
        <stop offset="0" stop-color="#4e4c49"/>
        <stop offset="1" stop-color="#2a2a2a"/>
      </linearGradient>
    </defs>
    <polygon points="196,843 357,843 277,922" fill="url(#chevronShade)"/>
    <polygon points="196,762 357,762 277,841" fill="var(--orange)" opacity="0.86"/>
  </svg>

  <section class="offer-panel">
    <p class="offer-kicker">What is Pay-Per-Use Production Space:</p>
    <h1 class="offer-headline">YOU USE IT,<br>YOU PAY IT<sup>**</sup></h1>
    <div class="offer-icons">
      <div class="offer-icon">
        <svg width="46" height="46" viewBox="0 0 46 46" fill="none" stroke="#fff" stroke-width="2">
          <path d="M4 42V14h6v28M10 42V24l10 6v-6l10 6v-6l10 6v12z"/>
          <path d="M14 36h4M22 36h4M30 36h4"/><path d="M2 42h42"/>
          <path d="M6 10c0-4 6-6 9-3 2-3 7-2 7 1"/>
        </svg>
      </div>
      <div class="offer-icon">
        <svg width="46" height="46" viewBox="0 0 46 46" fill="none" stroke="#fff" stroke-width="2">
          <path d="M4 4h38M10 4v8M34 4v8"/>
          <path d="M6 14l4-2 4 2M30 14l4-2 4 2"/>
          <rect x="8" y="20" width="8" height="8"/><rect x="30" y="18" width="8" height="8"/>
          <path d="M4 32h38v6H4z"/><circle cx="10" cy="35" r="1.5"/><circle cx="23" cy="35" r="1.5"/><circle cx="36" cy="35" r="1.5"/>
        </svg>
      </div>
      <div class="offer-icon">
        <svg width="46" height="46" viewBox="0 0 46 46" fill="none" stroke="#fff" stroke-width="2">
          <path d="M4 4h38M8 4v38M8 14l10 8 6-8M38 4v10l-4 6"/>
          <rect x="8" y="28" width="34" height="12"/>
          <path d="M14 34h22" stroke-dasharray="2 3"/>
        </svg>
      </div>
    </div>
    <p class="offer-terms">YOU DON’T USE THE<br>PRODUCTION SPACE,<br>YOU DON’T PAY FOR IT!<br>PARTIAL USE, PARTIAL PAY</p>
  </section>

  <h2 class="how-title">How can these work ?</h2>

  <div class="pillar pillar--design">
    <div class="pillar-badge">
      <svg width="50" height="50" viewBox="0 0 50 50" fill="none" stroke="#fff" stroke-width="1.8">
        <path d="M25 14a9 9 0 0 0-5 16v5h10v-5a9 9 0 0 0-5-16z"/>
        <path d="M21 38h8M22 41h6"/>
        <path d="M25 3v5M10 10l3 4M40 10l-3 4M4 22h5M41 22h5M9 35l3-3M41 35l-3-3"/>
        <circle cx="27" cy="22" r="3"/>
      </svg>
    </div>
    <p class="pillar-label">Through Our Patented<br>&amp; Innovative Factory<br>Space Design</p>
  </div>
  <div class="divider" style="left:424px"></div>
  <div class="pillar pillar--model">
    <div class="pillar-badge">
      <svg width="40" height="50" viewBox="0 0 40 50" fill="none" stroke="#fff" stroke-width="1.8">
        <path d="M6 18a14 14 0 0 1 28 0v10"/>
        <path d="M11 34V18a9 9 0 0 1 18 0v14"/>
        <path d="M16 40V18a4 4 0 0 1 8 0v18"/>
        <path d="M20 22v22M6 24v6"/>
      </svg>
    </div>
    <p class="pillar-label">Unique Business<br>Model</p>
  </div>
  <div class="divider" style="left:594px"></div>
  <div class="pillar pillar--practice">
    <div class="pillar-badge">
      <svg width="50" height="50" viewBox="0 0 50 50" fill="none" stroke="#fff" stroke-width="1.8">
        <path d="M12 6h26v14H12z"/><path d="M25 6v6a3 3 0 0 1 0 6"/>
        <path d="M6 30l8-6 8 4 6-4 8 4 8-4"/>
        <path d="M16 32l6 6 4-2 4 4 4-2"/>
        <path d="M12 22v6M38 22v6"/>
      </svg>
    </div>
    <p class="pillar-label">Due Diligence and Mutual<br>Adoption of Good Practises</p>
  </div>

  <p class="footnote">**Contact us for more details, case by case basis</p>
</body>
</html>
```